New Dental Office Needs an Attractive and user friendly Website Designed

I need a website for a new dental office. The Name is Harrowfield Dentistry. I would like a Modern design with a user friendly interface and usability.
I would like a landing page, a page that lists the services we offer: Cosmetic Dentistry, Implants, Dental Hygiene, Emergency Services, Restorations, Dentures
Target Market(s)
Mid to upper class
Industry/Entity Type
Dentistry
Coding
Number of Pages Required
1 page
Requirements
Must have
- Landing page that has a scheduling option, Procedures, operating hours, and contact us info
Nice to have
- Appealing design, Soft comforting colors. Easy to navigate page, Modern and professional.

```html
<!DOCTYPE html>
<html lang="en">
<head>
<meta charset="UTF-8">
<title>Harrowfield Dentistry</title>
<link href="https://fonts.googleapis.com/css2?family=Lexend:wght@400;500;600&family=Lato:wght@400;700&display=swap" rel="stylesheet">
<style>
:root{
  --blue:#4a8be0;
  --blue-soft:#dce9f9;
  --ink:#1f1f1f;
  --dark:#242424;
  --muted:#7a7a7a;
  --page:#f4f4f6;
  --card:#ffffff;
  --line:#d9d9de;
  --star:#f2b21b;
}
*{box-sizing:border-box;margin:0;padding:0}
html,body{width:1200px;height:3011px;overflow:hidden}
body{background:var(--page);font-family:'Lato',sans-serif;color:var(--ink);position:relative}
h1,h2,h3,.brand,.btn{font-family:'Lexend',sans-serif}
.accent{color:var(--blue)}
.abs{position:absolute}

/* nav */
.topbar{position:absolute;left:0;top:0;width:1200px;height:70px;background:var(--dark)}
.brand{position:absolute;left:150px;top:22px;color:#fff;font-size:20px;font-weight:500;letter-spacing:.3px}
.nav{position:absolute;right:141px;top:27px;display:flex;gap:29px}
.nav a{color:#fff;text-decoration:none;font-size:13px;font-family:'Lato',sans-serif}

/* hero */
.hero-wash{position:absolute;left:0;top:70px;width:606px;height:560px;background:linear-gradient(160deg,#eef1f6 0%,#dde7f3 35%,#f4f4f6 75%)}
.hero-photo{position:absolute;left:606px;top:70px;width:594px;height:424px;background:linear-gradient(120deg,#d7dce2 0%,#eeeae6 40%,#c9a98e 70%,#5fa49a 100%)}
.hero-title{position:absolute;left:141px;top:136px;width:440px;font-size:49px;line-height:49px;font-weight:600}
.hero-text{position:absolute;left:141px;top:301px;width:420px;font-size:12.5px;line-height:16px}
.btn{display:inline-block;border-radius:22px;font-size:12.5px;color:#fff;text-align:center;line-height:39px;height:39px}
.btn-blue{background:var(--blue)}
.btn-dark{background:var(--dark)}

.booking{position:absolute;left:812px;top:263px;width:247px;height:304px;background:#fff;border-radius:16px;box-shadow:0 6px 24px rgba(0,0,0,.06);padding:20px 21px}
.booking label{display:block;font-size:12px;font-weight:700;margin-bottom:8px}
.field{height:35px;background:#f2f2f4;border-radius:4px;margin-bottom:16px;display:flex;align-items:center;gap:8px;padding:0 9px;font-size:12px;color:var(--muted)}
.booking .btn{display:block;width:204px;margin-top:6px}

/* section heads */
.sec-title{position:absolute;left:0;width:1200px;text-align:center;font-size:28px;font-weight:500}
.sec-sub{position:absolute;left:0;width:1200px;text-align:center;font-size:12.5px;line-height:16px;color:var(--muted)}

/* services */
.service{position:absolute;width:293px;height:175px;background:var(--page);border:1.5px solid var(--line);border-radius:14px;text-align:center;padding:22px 20px 0}
.service.active{background:#fff;border:2px solid var(--blue)}
.service .ico{width:42px;height:42px;border-radius:50%;background:var(--blue-soft);margin:0 auto 11px;display:flex;align-items:center;justify-content:center}
.service.active .ico{background:var(--blue)}
.service h3{font-size:20px;font-weight:500;margin-bottom:6px}
.service.active h3{color:var(--blue)}
.service p{font-size:12.5px;line-height:15.5px;color:var(--muted)}
.service.active p{color:var(--ink)}

/* why */
.why{position:absolute;left:0;top:1193px;width:1200px;height:401px;background:var(--dark);color:#fff}
.why h2{position:absolute;left:141px;top:68px;font-size:28px;font-weight:500;line-height:37px}
.why .lead{position:absolute;left:141px;top:147px;width:265px;font-size:12.5px;line-height:16px}
.feat{position:absolute;width:300px}
.feat .head{display:flex;align-items:center;gap:13px}
.feat .ico{width:36px;height:36px;border-radius:50%;background:var(--blue-soft);display:flex;align-items:center;justify-content:center}
.feat h3{font-size:20px;font-weight:400}
.feat p{font-size:12.5px;line-height:16px;margin-top:8px}
.feat a{display:inline-block;margin-top:13px;font-size:12.5px;color:#fff}

/* visit */
.map{position:absolute;left:141px;top:1780px;width:642px;height:461px;background:linear-gradient(135deg,#a8c9ee 0%,#e5e3dc 45%,#c7dcf3 70%,#cde3c1 100%)}
.info{position:absolute;left:758px;top:1850px;width:301px;height:322px;background:var(--dark);border-radius:12px;color:#fff;padding:29px 28px}
.info h3{font-size:20px;font-weight:400;display:flex;align-items:center;gap:6px}
.info p{font-size:12.5px;line-height:16px;margin:6px 0 20px}
.info .btn-white{display:inline-block;background:#fff;color:var(--ink);border-radius:18px;height:31px;line-height:31px;padding:0 21px;font-size:12.5px}

/* testimonials */
.review{position:absolute;top:2433px;width:448px;height:190px;background:#e7eef8;border-radius:12px;padding:20px 21px}
.review .stars{display:flex;gap:5px}
.review .date{position:absolute;right:21px;top:24px;font-size:12.5px}
.review .quote{font-size:12.5px;line-height:16px;margin-top:18px;width:400px}
.person{display:flex;align-items:center;gap:13px;margin-top:18px}
.avatar{width:57px;height:57px;border-radius:50%}
.person strong{display:block;font-family:'Lexend',sans-serif;font-weight:400;font-size:20px}
.person span{font-size:12.5px;color:var(--muted)}
.arrow{position:absolute;top:2518px;width:28px;height:28px;border-radius:5px;display:flex;align-items:center;justify-content:center}

/* footer */
.footer{position:absolute;left:0;top:2769px;width:1200px;height:242px;background:var(--dark);color:#fff}
.footer .brand{left:0;width:1200px;text-align:center;top:65px;font-size:22px}
.footer .nav{right:auto;left:0;width:1200px;justify-content:center;top:126px}
.footer .rule{position:absolute;left:0;top:199px;width:1200px;height:1px;background:#3d3d3d}
.footer .copy{position:absolute;left:0;top:213px;width:1200px;text-align:center;font-size:11px}
</style>
</head>
<body>

<header class="topbar">
  <div class="brand">Harrowfield Dentistry</div>
  <nav class="nav"><a href="#">Home</a><a href="#">Our Services</a><a href="#">Contact Us</a></nav>
</header>

<section class="hero">
  <div class="hero-wash"></div>
  <div class="hero-photo" role="img" aria-label="Smiling patient with a dentist giving a thumbs up in a bright clinic"></div>
  <h1 class="hero-title">Premium <span class="accent">Dental Care</span> for a Confident Smile</h1>
  <p class="hero-text">Experience expert cosmetic, restorative, and emergency treatments in a calm, comfort-first environment tailored to your needs.</p>
  <a class="btn btn-blue abs" style="left:141px;top:389px;width:127px">Call Us Now</a>
  <a class="btn btn-dark abs" style="left:282px;top:389px;width:127px">View Services</a>

  <form class="booking">
    <label>Full Name</label>
    <div class="field"><svg width="13" height="13" viewBox="0 0 24 24" fill="none" stroke="#888" stroke-width="2"><circle cx="12" cy="8" r="4"/><path d="M4 21c1-5 15-5 16 0"/></svg>John Dee</div>
    <label>Phone</label>
    <div class="field"><svg width="13" height="13" viewBox="0 0 24 24" fill="none" stroke="#888" stroke-width="2"><path d="M5 3h4l2 5-3 2a12 12 0 006 6l2-3 5 2v4a2 2 0 01-2 2A18 18 0 013 5a2 2 0 012-2z"/></svg>Your Phone</div>
    <label>Preferred Date</label>
    <div class="field"><svg width="13" height="13" viewBox="0 0 24 24" fill="none" stroke="#888" stroke-width="2"><rect x="3" y="5" width="18" height="16" rx="2"/><path d="M3 10h18M8 3v4M16 3v4"/></svg>dd/mm/yyy</div>
    <a class="btn btn-blue">Book Now</a>
  </form>
</section>

<h2 class="sec-title" style="top:624px">Our Dental <span class="accent">Services</span></h2>
<p class="sec-sub" style="top:667px">Comprehensive, high-quality care from cosmetic enhancements to<br>emergency treatments—tailored to your smile.</p>

<div class="service" style="left:141px;top:738px">
  <div class="ico"><svg width="24" height="24" viewBox="0 0 24 24" fill="none" stroke="#4a8be0" stroke-width="1.6"><circle cx="12" cy="12" r="9"/><path d="M8 14c2 3 6 3 8 0"/><circle cx="9" cy="10" r=".8"/><circle cx="15" cy="10" r=".8"/></svg></div>
  <h3>Cosmetic Dentistry</h3><p>Enhance your smile with treatments that improve tooth shape, color, and appearance.</p>
</div>
<div class="service active" style="left:455px;top:738px">
  <div class="ico"><svg width="24" height="24" viewBox="0 0 24 24" fill="none" stroke="#fff" stroke-width="1.6"><path d="M7 4c2-1 3 1 5 1s3-2 5-1 1 6-1 7H8C6 10 5 5 7 4z"/><path d="M9 13h6M10 16h4M11 19h2"/></svg></div>
  <h3>Dental Implants</h3><p>Permanent, natural-looking tooth replacements that restore function and confidence.</p>
</div>
<div class="service" style="left:768px;top:738px">
  <div class="ico"><svg width="24" height="24" viewBox="0 0 24 24" fill="none" stroke="#4a8be0" stroke-width="1.6"><path d="M5 5l14 14M19 5L5 19"/><circle cx="5" cy="5" r="2"/><circle cx="19" cy="5" r="2"/></svg></div>
  <h3>Emergency Services</h3><p>Quick, professional treatment for dental emergencies, providing relief when you need it most.</p>
</div>
<div class="service" style="left:141px;top:949px">
  <div class="ico"><svg width="24" height="24" viewBox="0 0 24 24" fill="none" stroke="#4a8be0" stroke-width="1.6"><path d="M3 9c6-3 12-3 18 0-2 6-16 6-18 0z"/><path d="M8 10v3M12 10v3M16 10v3"/></svg></div>
  <h3>Dentures</h3><p>Comfortable, custom-fitted full and partial dentures that restore your bite and smile.</p>
</div>
<div class="service" style="left:455px;top:949px">
  <div class="ico"><svg width="24" height="24" viewBox="0 0 24 24" fill="none" stroke="#4a8be0" stroke-width="1.6"><path d="M6 4c3-1 4 1 6 1s3-2 6-1 1 8-1 12-3 4-3 0-1-3-2-3-1 7-3 3S3 5 6 4z"/><path d="M18 2l1 2 2 1-2 1-1 2-1-2-2-1 2-1z"/></svg></div>
  <h3>Dental Hygiene</h3><p>Preventive cleanings and exams to keep your teeth and gums healthy, fresh, and cavity-free.</p>
</div>
<div class="service" style="left:768px;top:949px">
  <div class="ico"><svg width="24" height="24" viewBox="0 0 24 24" fill="none" stroke="#4a8be0" stroke-width="1.6"><path d="M6 4c3-1 4 1 6 1s3-2 6-1 1 8-1 12-3 4-3 0-1-3-2-3-1 7-3 3S3 5 6 4z"/></svg></div>
  <h3>Tooth Restoration</h3><p>Repair and restore damaged teeth with natural-looking fillings, crowns, and bridges for a healthier smile.</p>
</div>

<section class="why">
  <h2>Why Patients<br>Choose <span class="accent">Our Clinic</span></h2>
  <p class="lead">Experience expert care in a modern, comfort-first clinic—where advanced technology meets personalized treatment.</p>

  <div class="feat" style="left:443px;top:70px">
    <div class="head"><div class="ico"><svg width="18" height="18" viewBox="0 0 24 24" fill="none" stroke="#4a8be0" stroke-width="2"><rect x="4" y="6" width="16" height="12" rx="2"/><circle cx="12" cy="12" r="3"/></svg></div><h3>Board-Certified Dentists</h3></div>
    <p>Expertise you can trust, backed by advanced training and credentials.</p><a href="#">Learn more</a>
  </div>
  <div class="feat" style="left:765px;top:70px">
    <div class="head"><div class="ico"><svg width="18" height="18" viewBox="0 0 24 24" fill="none" stroke="#4a8be0" stroke-width="2"><path d="M7 4c2-1 3 1 5 1s3-2 5-1 1 7-1 11-3 4-3 0-1-3-1-3-1 7-3 3S5 5 7 4z"/></svg></div><h3>Pain-Free Treatments</h3></div>
    <p>Gentle techniques and modern technology for a stress-free experience.</p><a href="#">Learn more</a>
  </div>
  <div class="feat" style="left:443px;top:228px">
    <div class="head"><div class="ico"><svg width="18" height="18" viewBox="0 0 24 24" fill="none" stroke="#4a8be0" stroke-width="2"><path d="M5 18c3 0 4-3 6-6s5-5 8-5"/><circle cx="12" cy="12" r="8"/></svg></div><h3>Luxury, Comfort Clinic</h3></div>
    <p>Designed to help you relax—because your comfort matters.</p><a href="#">Learn more</a>
  </div>
  <div class="feat" style="left:765px;top:228px">
    <div class="head"><div class="ico"><svg width="18" height="18" viewBox="0 0 24 24" fill="none" stroke="#4a8be0" stroke-width="2"><rect x="4" y="7" width="16" height="12" rx="2"/><path d="M7 7l8-3 2 3M15 13h5"/></svg></div><h3>Flexible Payment Plans</h3></div>
    <p>Quality care made accessible with tailored financing options.</p><a href="#">Learn more</a>
  </div>
</section>

<h2 class="sec-title" style="top:1664px">Visit Our <span class="accent">Clinic</span></h2>
<p class="sec-sub" style="top:1707px">Located in the heart of Harrowfield, our clinic offers<br>flexible hours and easy access to premium dental care.</p>

<div class="map" role="img" aria-label="Street map showing the clinic location and surrounding neighbourhoods"></div>
<div class="info">
  <h3><svg width="18" height="18" viewBox="0 0 24 24" fill="none" stroke="#4a8be0" stroke-width="2"><path d="M12 21s-7-7-7-12a7 7 0 0114 0c0 5-7 12-7 12z"/><circle cx="12" cy="9" r="2.5"/></svg>Visit Us</h3>
  <p style="padding-left:8px">48 Willowmere Road, Harrowfield</p>
  <h3><svg width="18" height="18" viewBox="0 0 24 24" fill="none" stroke="#4a8be0" stroke-width="2"><circle cx="12" cy="12" r="9"/><path d="M12 7v5l3 2"/></svg>Operating Hours</h3>
  <p>Mon–Fri: 8:00 AM – 6:00 PM<br>Sat: 9:00 AM – 2:00 PM<br>Closed Sundays</p>
  <h3><svg width="18" height="18" viewBox="0 0 24 24" fill="none" stroke="#4a8be0" stroke-width="2"><path d="M5 3h4l2 5-3 2a12 12 0 006 6l2-3 5 2v4a2 2 0 01-2 2A18 18 0 013 5a2 2 0 012-2z"/></svg>Call Us</h3>
  <p>(555) 014-2236</p>
  <a class="btn-white">Call Now</a>
</div>

<h2 class="sec-title" style="top:2310px">What Our <span class="accent">Patients Say</span></h2>
<p class="sec-sub" style="top:2353px;color:var(--ink)">Real stories from patients who’ve experienced compassionate care,<br>outstanding results, and a confident new smile.</p>

<div class="arrow" style="left:91px;border:1.5px solid var(--ink)"><svg width="12" height="12" viewBox="0 0 24 24" fill="none" stroke="#1f1f1f" stroke-width="2.5"><path d="M15 4l-8 8 8 8"/></svg></div>
<div class="arrow" style="left:1080px;background:var(--dark)"><svg width="12" height="12" viewBox="0 0 24 24" fill="none" stroke="#fff" stroke-width="2.5"><path d="M9 4l8 8-8 8"/></svg></div>

<div class="review" style="left:141px">
  <div class="stars">
    <svg width="21" height="21" viewBox="0 0 24 24"><path fill="#f2b21b" d="M12 2l3 7h7l-6 5 2 8-6-4-6 4 2-8-6-5h7z"/></svg><svg width="21" height="21" viewBox="0 0 24 24"><path fill="#f2b21b" d="M12 2l3 7h7l-6 5 2 8-6-4-6 4 2-8-6-5h7z"/></svg><svg width="21" height="21" viewBox="0 0 24 24"><path fill="#f2b21b" d="M12 2l3 7h7l-6 5 2 8-6-4-6 4 2-8-6-5h7z"/></svg><svg width="21" height="21" viewBox="0 0 24 24"><path fill="#f2b21b" d="M12 2l3 7h7l-6 5 2 8-6-4-6 4 2-8-6-5h7z"/></svg><svg width="21" height="21" viewBox="0 0 24 24"><path fill="#f2b21b" d="M12 2l3 7h7l-6 5 2 8-6-4-6 4 2-8-6-5h7z"/></svg>
  </div>
  <span class="date">10th Feb, 2023</span>
  <p class="quote">"The team made me feel comfortable from the moment I walked in. My smile has never looked better!"</p>
  <div class="person"><div class="avatar" role="img" aria-label="Portrait photo of the patient" style="background:linear-gradient(135deg,#cfcfcf,#6d6259)"></div><div><strong>Daniel R.</strong><span>Customer</span></div></div>
</div>
<div class="review" style="left:611px">
  <div class="stars">
    <svg width="21" height="21" viewBox="0 0 24 24"><path fill="#f2b21b" d="M12 2l3 7h7l-6 5 2 8-6-4-6 4 2-8-6-5h7z"/></svg><svg width="21" height="21" viewBox="0 0 24 24"><path fill="#f2b21b" d="M12 2l3 7h7l-6 5 2 8-6-4-6 4 2-8-6-5h7z"/></svg><svg width="21" height="21" viewBox="0 0 24 24"><path fill="#f2b21b" d="M12 2l3 7h7l-6 5 2 8-6-4-6 4 2-8-6-5h7z"/></svg><svg width="21" height="21" viewBox="0 0 24 24"><path fill="#f2b21b" d="M12 2l3 7h7l-6 5 2 8-6-4-6 4 2-8-6-5h7z"/></svg><svg width="21" height="21" viewBox="0 0 24 24"><path fill="#f2b21b" d="M12 2l3 7h7l-6 5 2 8-6-4-6 4 2-8-6-5h7z"/></svg>
  </div>
  <span class="date">06th Feb, 2023</span>
  <p class="quote">"Beautiful clinic, friendly staff, and pain-free treatment. Truly a premium dental experience."</p>
  <div class="person"><div class="avatar" role="img" aria-label="Portrait photo of the patient" style="background:linear-gradient(135deg,#e6c34a,#c99a7a)"></div><div><strong>Maya K.</strong><span>Customer</span></div></div>
</div>

<a class="btn btn-blue abs" style="left:547px;top:2674px;width:105px">View All</a>

<footer class="footer">
  <div class="brand">Harrowfield Dentistry</div>
  <nav class="nav"><a href="#">Home</a><a href="#">Our Services</a><a href="#">Contact Us</a></nav>
  <div class="rule"></div>
  <p class="copy">© 2025 Harrowfield Dental Care. All Rights Reserved.</p>
</footer>

</body>
</html>
```